verdant terraces simple classy business card design

my name is colin barrow and I run a gardening business aimed at high class verdant terraces. the business name is verdant terraces and our logo was designed on pixel harbour .My clientel are anything from residential homes to businesses. I take pride in my work and know that I offer a service like no other in my area.
The business card will be used to represent my business and I want it to be not only rememberable, but simplistic and modern. Eye catching too. Of course I would like it relatable to gardening and appealing to the correct clientel - those being garden enthusiasts, prestigious homes and businesses that are after top of the line gardening services like no other on the market.
I am not a typical lawn mowing business so I don't want a typical card design that represents that. The gardens I work with are generally million dollar properties with owners who are very garden proud looking for upkeep and guidance from me along with sometimes whole new garden designs. I want the business cards to show to my clients that I take pride, as they do, in their garden. And I want them to know from my card that I am a professional, qualified horticulturist offering them a top of the line service for life. I want them to refer my business on. I want them to look at my business card and see class and professionalism in a modern unique bold way.
The card should be simple with the possibility of the logo on the front being embossed/debossed and my details on the back the card should have a organic garden feel it's very important to me that it is absolutely perfect
I am also very open to ideas and suggestions so look forward to seeing the designs. the business logo has been supplied with this project and I want the card to be double sided

Contact info is
Colin Barrow - Managing Director / Horticulturist
Phone : 0481 526 704
Email: colinbarrow@verdantterraces.example.au

Target Market(s)

high class gardens residential and commercial

Industry/Entity Type

Gardener

Contact Information for Business Card

Contact info is
Phone : 0481 526 704

PLEASE MAKE CARD DOUBLE SIDED

Requirements
Must have
• organic simple classy modern feel
• must flow with the current logo that has been supplied with this project
• Double sided
• Must explain in a simple way that I deal with high end gardens and I'm a qualified horticulturist
Nice to have
• embossed debossed logo
Should not have
• shouldn't be to busy or cheap looking

```html
<!DOCTYPE html>
<html lang="en">
<head>
<meta charset="utf-8">
<title>Verdant Terraces — Business Card</title>
<link rel="stylesheet" href="https://fonts.googleapis.com/css2?family=Source+Sans+3:wght@400;500&display=swap">
<style>
  :root {
    --bg: #eceeee;
    --card: #ffffff;
    --green: #5d9a4e;
    --divider: #555555;
    --frame: #6a6a6a;
    --sky: #2f6fc4;
    --hedge: #2f6a22;
    --hedge-light: #4f8a32;
    --stone: #d8c7a8;
  }
  * { box-sizing: border-box; margin: 0; padding: 0; }
  html, body { width: 1200px; height: 854px; overflow: hidden; }
  body {
    background: var(--bg);
    font-family: "Source Sans 3", "Myriad Pro", Arial, sans-serif;
    position: relative;
  }
  .card {
    position: absolute;
    top: 278px;
    width: 522px;
    height: 297px;
    background: var(--card);
    box-shadow: 0 2px 6px rgba(0,0,0,0.18);
  }
  .card--details { left: 43px; }
  .card--feature { left: 625px; border: 4px solid var(--frame); overflow: hidden; }

  .details__divider {
    position: absolute;
    left: 281px; top: 16px;
    width: 3px; height: 264px;
    background: var(--divider);
  }
  .details__name {
    position: absolute; right: 276px; top: 114px;
    font-size: 25px; font-weight: 400; color: var(--green);
    white-space: nowrap;
  }
  .details__role {
    position: absolute; right: 276px; top: 160px;
    font-size: 13.5px; color: var(--green); white-space: nowrap;
  }
  .details__contact {
    position: absolute; right: 258px; top: 234px;
    text-align: right; font-size: 12.5px; line-height: 17px;
    color: var(--green); white-space: nowrap;
  }
  .brand {
    display: flex; flex-direction: column; align-items: center;
    color: var(--green);
  }
  .brand__dot {
    width: 48px; height: 48px; border-radius: 50%;
    background: var(--green);
  }
  .brand__name {
    margin-top: 8px;
    font-size: 21px; font-weight: 500; letter-spacing: 2px;
    text-transform: uppercase; white-space: nowrap; line-height: 1;
  }
  .details__brand {
    position: absolute; left: 299px; width: 223px; top: 92px;
  }
  .feature__photo {
    position: absolute; inset: 0;
    background: linear-gradient(180deg,
      var(--sky) 0%, var(--stone) 20%, var(--stone) 38%,
      var(--hedge-light) 46%, var(--hedge) 70%, var(--hedge-light) 88%, #8a8a80 100%);
  }
  .feature__tab {
    position: absolute; left: 169px; top: -4px;
    width: 171px; height: 113px;
    background: var(--card);
    border-radius: 0 0 8px 8px;
    display: flex; align-items: center; justify-content: center;
  }
  .feature__tab .brand__dot { width: 36px; height: 36px; }
  .feature__tab .brand__name { font-size: 15px; letter-spacing: 1.2px; margin-top: 7px; }
</style>
</head>
<body>
  <section class="card card--details">
    <p class="details__name">Colin Barrow</p>
    <p class="details__role">Managing Director / Horticulturist</p>
    <p class="details__contact">Phone : 0481 526 704<br>Email: colinbarrow@verdantterraces.example.au</p>
    <div class="details__divider"></div>
    <div class="brand details__brand">
      <span class="brand__dot"></span>
      <span class="brand__name">Verdant Terraces</span>
    </div>
  </section>

  <section class="card card--feature">
    <div class="feature__photo" role="img" aria-label="Photograph of a manor house above terraced formal gardens with clipped hedges and a central stone staircase"></div>
    <div class="feature__tab">
      <div class="brand">
        <span class="brand__dot"></span>
        <span class="brand__name">Verdant Terraces</span>
      </div>
    </div>
  </section>
</body>
</html>
```